Website front end design for an education nonprofit

This project involves design and development of the website front end (i.e., Web user interface and user experience design) for TAVO Sphere, a nonprofit initiative for developing an online platform for basic English language instruction, especially targeted toward underprivileged, non-native English speaking populations.

More about us: We are a team of educators, researchers and engineers passionate about this cause and would like to invite talented, creative web developers to join us in this effort to create positive social impact! Please send a personal message to the project owner for the executive summary to get more information about our initiative, big picture vision and the team.

TAVO Sphere website front end (UI/UX) design
Our key goals for this project are to develop an impressive Drupal-based front end for our website as well as to find really talented and creative web/UI/UX designers-cum-developers who are experts in the state-of-the-art web technologies, and are passionate about the cause of global online basic education. At the end of this project, we hope to have long term engagement with the selected developer(s) for our future website design and development needs.

Here are some preliminary guidelines on the TAVO Sphere website front end framework as envisioned by us so far. Please note that we would very much encourage creative ideas and mock-ups from the developers.

1. Current platform: Our website prototype back-end uses Drupal CMS (we plan to continue using Drupal CMS) and at the moment, a toy front-end is based on the Drupal Skeleton platform for its simplicity, clean UI and mobile device friendliness. The web developer / designer can choose any Drupal front end as a starting point or come up with a new Drupal template that meets our requirements below. Prior experience and expertise on Drupal would be great.

2. Audience profile: While the primary audience for the website is expected to be young kids (6-10 years) not very familiar with English, the secondary audience also includes adults interested in basic English language skills. So the overall goal is to have simple, uncluttered / clean, elegant and lightweight (think loading time as well as mobile device friendliness) interface that is extremely intuitive and easy to navigate, is artistic and aesthetically appealing to a wide audience (especially the non-native English speaking populations). The most important point is that our target audience should feel welcome with the clean, crisp look and easy, user-centric navigation, and should in no case feel overwhelmed (say with too much text or clutter on the front page).

3. Front page: Here is a currently envisioned preliminary sketch of the website front page (very much open for refinement and improvements)
a. The top “menu bar” part of the landing page will have our organization name and logo along with (or above) the top menu bar with the following links and sub-links
i. “Learn” link with sub-menu of all our content sections (World learning, Basic sentence learning, Classic short stories, Picture Dictionary)
ii. “About” links with information about us (sub-menu entries: About TAVO Sphere, Team, Supporters, Contributors)
iii. “Contribute” link with sub-menu entries Donate, Volunteer
iv. Menu entries towards the right side: “Login / sign up” followed by
v. “Search” with space to enter the search phrase
b. The middle “main page content” part of the page is where we would have entry points to our main content categories. The portion is envisioned to be graphical, with big blocks (images) as links to our content categories. The current categories (to start with) include 1. Word learning, 2. Basic sentence learning, and 3. Classic stories. We welcome creative ideas to represent these content categories in an appealing and elegant way (for example, these content categories could be portrayed as closed double doors that lead to the pages with the content. We would like to have placeholders for appropriate image links to different content categories – we should be able to put appropriate images or change them as we come up with new ideas that would work best with our target audience). The categories would change and grow as our content evolves, hence the core idea is to build a flexible framework that readily allows for expansion as well as customization.
c. The bottom menu / links bar portion of the landing page will have a list of links that are not included at the top. Examples include (with flexibility needed to add more when needed)
i. “Help”: this leads to a new page with FAQ, How to use
ii. “Contact us” link to a web contact form page
iii. “For Teachers” link to a page with information such as how to use, tips, pilot programs,
iv. “Volunteer” link to page with links such as Donate, Volunteer
v. “Contributors” that would link to a page with information about our Artists, Teachers, Writers, Developers etc.
vi. “Jobs” would link to a jobs page
vii. “Blog” would lead to our blog page
viii. “User stories” link to pages with feedback that we obtain from the users about how the content has helped them,
ix. Web 2.0 placeholders for social media (to be added later)

d. The footer of the website should include text “2013 TAVO Sphere, All rights reserved.”

4. The middle block of the front page is the largest in screen real estate and perhaps the most challenging part that requires much creativity and thought on the UI/UX design aspect – the content pages pointed to by the section links on the middle portion of the front page are also being designed.

5. Color preference is towards soft, elegant (think grays, whites, light blues, other light colors) web safe colors. No harsh (too bright, garish) colors.

6. Fonts preference Nice, clean looking fonts (Arial alright) compatible across browsers.

7. Portability and robustness of the front page layout for different platforms should be carefully considered. Although our first launch target platform is PC (where cross browser compatibility is important), this would very soon be followed by mobile devices such as tablets and smartphones given their prevalence across the globe. This mobile friendly design or easy portability to mobile platforms with little work requirement should be considered as a design requirement.

8. Front page as a framework for the complete website: Note that the top and the bottom portions of the front page are envisioned be used as a common template / frame across all the pages of our website – the middle portion would be used to show our content on the other pages of our website.

9. UX: For the UI/UX design, it is critical to keep in mind key qualities such as ease of use, simplicity, elegance and artistic appeal. Some specific points to keep in mind: (1) the major portion of the target audience would be new to English and (2) young children are expected to be the primary audience but we want the website to appeal to adults interested in learning as well, and (3) we need the website to work even with relatively slow Internet speeds (for underdeveloped / developing regions especially), should always be kept in mind. HTML5 compliance ideas are encouraged.

10. Strictly not desired: Typical corporate feel seen in many webpages, blocky graphics, dull and uninviting overall look with no personality, Flash type effects, harsh colors.

11. Creativity and imagination necessary: We would like to reiterate that the designer/developer has complete freedom to re-imagine the front page considering the above requirements and get back with ideas for an inspiring layout that presents the content outlined above in an intuitive format, carefully considering our target audience.

A note: As a rule, we will always make sure that our developers and artists get proper credit for their work and are recognized and acknowledged by everyone visiting our website.

Expected deliverables:
Website design psd files AND coded webpage / Drupal template: the corresponding source code and all the required libraries, images etc would be required with minimal documentation / pointers on how to make changes and customizations.

Interested developers are encouraged to first send us preliminary prototype Design for the front page to get feedback on whether their approach and style is in line with our needs and preferences. We will suggest the developers to proceed further if the team thinks there is some potential for a match (of course, the final determination would be from the pool of shortlisted submissions) – otherwise, in case the team does not see potential for a match with our needs or if we have already received multiple submissions that are comparatively more closely aligned with our vision for the website, we'd prefer to be respectful of the developers’ time and effort by requesting them not to proceed further.

Please consider this effort as your contribution to an important social cause of global and accessible online education and not a commercial enterprise (our passion for making a positive impact is what is driving the TAVO Sphere nonprofit team to undertake this initiative!). We would like to invite you to join us in this effort!

Project Deadline Extended
Reason: Due to requests from interested designers, we are extending the deadline. Looking forward to receiving many other creative designs!

Please see the project brief.

Real Estate

• Please see the project brief.

```html
<!DOCTYPE html>
<html lang="en">
<head>
<meta charset="utf-8">
<title>TAVO Sphere — Learn Basic English</title>
<link href="https://fonts.googleapis.com/css2?family=Ubuntu:wght@400;500&display=swap" rel="stylesheet">
<style>
:root{
  --blue:#1e8fe0;
  --blue-dark:#1378c8;
  --blue-light:#3aa3ee;
  --ink:#333;
  --text:#555;
  --white:#fff;
  --footer:#666;
  --footer-dark:#3d3d3d;
  --orange:#f57d20;
  --line:#dcdcdc;
}
*{box-sizing:border-box;margin:0;padding:0}
html,body{width:1143px;height:1200px;overflow:hidden;background:var(--white)}
body{position:relative;font-family:"Ubuntu",Arial,sans-serif;color:var(--text)}
.abs{position:absolute}

/* header */
.brand{left:120px;top:26px;font-size:30px;font-weight:500;color:var(--blue);text-transform:uppercase;letter-spacing:.5px}
.call{left:824px;top:36px;width:20px;height:24px;background:#111;border-radius:3px}
.call svg{display:block;margin:3px auto}
.call-label{left:870px;top:20px;font-size:16px;color:var(--blue)}
.call-number{left:870px;top:42px;font-size:21px;color:#111}

/* nav */
.nav{left:0;top:85px;width:1143px;height:47px;background:linear-gradient(var(--blue-light),var(--blue-dark));border-bottom:2px solid #0f6cb8}
.nav a{position:absolute;top:0;height:45px;line-height:45px;color:var(--white);font-size:15px;text-decoration:none;padding:0 22px;border-right:1px solid rgba(0,0,0,.12)}
.search{left:672px;top:10px;width:209px;height:26px;background:var(--white);border:1px solid #b9d4ea;font-size:10px;color:#999;line-height:24px;padding-left:7px}
.search svg{position:absolute;right:6px;top:6px}
.search::after{content:"";position:absolute;right:28px;top:2px;bottom:2px;border-left:1px solid #ddd}
.btn-login{left:891px;top:10px;width:47px;height:26px;background:var(--blue);border:1px solid #7cc0f2;color:#fff;font-size:12px;text-align:center;line-height:24px}
.btn-signup{left:960px;top:10px;width:69px;height:26px;background:#555;border:1px solid #888;color:#fff;font-size:12px;text-align:center;line-height:24px}

/* hero */
.hero{left:0;top:132px;width:1143px;height:417px;background:radial-gradient(ellipse at 55% 45%,#e9b890 0%,#c98d5c 30%,#6a7fa0 60%,#2e6fb8 100%)}
.hero-caption{left:114px;top:305px;width:457px;height:71px;background:var(--blue);color:#fff;font-size:33px;line-height:71px;padding-left:21px;letter-spacing:.5px}
.dots{left:545px;top:531px}
.dots span{display:inline-block;width:9px;height:9px;border-radius:50%;background:#bbb;border:1px solid #888;margin-right:5px}
.dots span:first-child{background:#555}

/* tiles */
.tile{top:565px;width:284px;height:151px}
.tile .photo{height:116px}
.tile .label{height:35px;background:var(--blue);color:#fff;font-size:16px;line-height:35px;padding-left:20px;position:relative}
.tile .label svg{position:absolute;right:10px;top:12px}

/* content */
h2{position:absolute;font-size:21px;font-weight:500;color:var(--ink)}
.welcome-photo{left:115px;top:775px;width:257px;height:173px;background:linear-gradient(135deg,#f3c9a6,#d99b70 60%,#b5704a)}
.body-text{left:380px;width:336px;font-size:11.5px;line-height:16.2px;text-align:justify;color:#666}
.read-more{width:76px;height:30px;background:var(--blue);color:#fff;font-size:11px;text-align:center;line-height:30px}
.post-thumb{left:742px;width:74px;height:74px}
.post{left:826px;width:203px}
.post .title{font-size:12.5px;color:var(--blue)}
.post .date{font-size:11px;color:#333;margin:3px 0 5px}
.post p{font-size:11.3px;line-height:15px;text-align:justify;color:#666}
.post-rule{left:742px;top:866px;width:287px;border-top:1px solid var(--line)}

/* footer */
.footer{left:0;top:1012px;width:1143px;height:140px;background:var(--footer)}
.footer h3{position:absolute;font-size:12.5px;font-weight:400;color:#fff;text-transform:uppercase}
.footer ul{position:absolute;list-style:none;font-size:10.8px;color:#fff}
.footer li{height:22.8px}
.social li{padding-left:30px;position:relative}
.social li i{position:absolute;left:0;top:1px;width:12px;height:12px;background:#fff;border-radius:2px}
.cta{left:819px;width:210px;height:44px;color:#fff;font-size:22px;line-height:42px;padding-left:60px;border:1px solid rgba(255,255,255,.5)}
.cta i{position:absolute;left:12px;top:8px;width:26px;height:26px;border-radius:50%;background:rgba(255,255,255,.85)}
.cta-donate{top:1032px;background:linear-gradient(var(--blue-light),var(--blue-dark))}
.cta-volunteer{top:1091px;background:linear-gradient(#fb9540,var(--orange))}
.bottom{left:0;top:1152px;width:1143px;height:48px;background:var(--footer-dark);color:#fff;font-size:11px;text-align:center;line-height:48px}
</style>
</head>
<body>

<header>
  <div class="abs brand">TAVO Sphere</div>
  <div class="abs call"><svg width="12" height="18" viewBox="0 0 12 18"><path d="M3 1h3v5H4v6h2v5H3C1 15 1 3 3 1z" fill="#fff"/></svg></div>
  <div class="abs call-label">CALL US NOW!</div>
  <div class="abs call-number">(000) 000 0000</div>
</header>

<nav class="abs nav">
  <a style="left:115px">LEARN</a>
  <a style="left:207px">ABOUT</a>
  <a style="left:303px">CONTRIBUTE</a>
  <div class="abs search">Search here<svg width="12" height="12" viewBox="0 0 12 12"><circle cx="5" cy="5" r="3.5" fill="none" stroke="#aaa" stroke-width="1.5"/><path d="M7.5 7.5l3.5 3.5" stroke="#aaa" stroke-width="1.5"/></svg></div>
  <div class="abs btn-login">LOGIN</div>
  <div class="abs btn-signup">SIGN UP</div>
</nav>

<section>
  <div class="abs hero" role="img" aria-label="Children drawing with coloured pencils in a classroom"></div>
  <div class="abs hero-caption">BASIC SENTENCE LEARNING</div>
  <div class="abs dots"><span></span><span></span><span></span><span></span></div>
</section>

<section>
  <div class="abs tile" style="left:115px">
    <div class="photo" role="img" aria-label="Teacher in front of a chalkboard" style="background:linear-gradient(135deg,#9fb5a8,#6f8f80 55%,#e8e8e8)"></div>
    <div class="label">FOR TEACHERS<svg width="18" height="11" viewBox="0 0 18 11"><path d="M1 1l5 4.5L1 10M9 1l5 4.5L9 10" fill="none" stroke="#fff" stroke-width="2.4"/></svg></div>
  </div>
  <div class="abs tile" style="left:429px">
    <div class="photo" role="img" aria-label="Smiling child holding letter blocks" style="background:linear-gradient(180deg,#6f9a3a,#b78a5a 60%,#c44a3a)"></div>
    <div class="label">BASIC SENTENCE LEARNING<svg width="18" height="11" viewBox="0 0 18 11"><path d="M1 1l5 4.5L1 10M9 1l5 4.5L9 10" fill="none" stroke="#fff" stroke-width="2.4"/></svg></div>
  </div>
  <div class="abs tile" style="left:742px">
    <div class="photo" role="img" aria-label="Teacher reading a book with two children" style="background:linear-gradient(135deg,#d9b99a,#e6d3c0 45%,#c25a9a)"></div>
    <div class="label">USER STORIES<svg width="18" height="11" viewBox="0 0 18 11"><path d="M1 1l5 4.5L1 10M9 1l5 4.5L9 10" fill="none" stroke="#fff" stroke-width="2.4"/></svg></div>
  </div>
</section>

<main>
  <h2 style="left:115px;top:731px">Welcome to TAVO Sphere!</h2>
  <div class="abs welcome-photo" role="img" aria-label="Colourful wooden letter blocks"></div>
  <p class="abs body-text" style="top:773px">Sed ut perspiciatis unde omnis iste natus error sit voluptatem accusantium doloremque laudantium, totam rem aperiam, eaque ipsa quae ab illo inventore veritatis et quasi architecto beatae vitae dicta sunt explicabo. Nemo enim ipsam voluptatem quia voluptas sit aspernatur aut odit aut fugit, sed quia consequuntur magni dolores eos qui ratione voluptatem sequi nesciunt.</p>
  <p class="abs body-text" style="top:887px">Neque porro quisquam est, qui dolorem ipsum quia dolor sit amet, consectetur, adipisci velit, sed quia non numquam eius modi tempora incidunt ut labore et dolore magnam aliquam quaerat voluptatem.</p>
  <div class="abs read-more" style="left:115px;top:959px">READ MORE</div>

  <h2 style="left:742px;top:731px">Recent Blog</h2>
  <div class="abs post-thumb" style="top:776px;background:linear-gradient(135deg,#8a9a7a,#e9e4da)" role="img" aria-label="Student reading at a desk"></div>
  <div class="abs post" style="top:773px">
    <div class="title">Sed ut perspiciatis unde omnis iste</div>
    <div class="date">July 25, 2013</div>
    <p>natus error sit voluptatem accusantium doloremque laudantium, totam rem aperiam, eaque ipsa quae ab illo inven-</p>
  </div>
  <div class="abs post-rule"></div>
  <div class="abs post-thumb" style="top:874px;background:linear-gradient(135deg,#c9b8a8,#7d8fa8)" role="img" aria-label="Group of students with books"></div>
  <div class="abs post" style="top:871px">
    <div class="title">Sed ut perspiciatis unde omnis iste</div>
    <div class="date">July 25, 2013</div>
    <p>natus error sit voluptatem accusantium doloremque laudantium, totam rem aperiam, eaque ipsa quae ab illo inven-</p>
  </div>
  <div class="abs read-more" style="left:742px;top:959px">READ MORE</div>
</main>

<footer>
  <div class="abs footer">
    <h3 style="left:115px;top:18px">Quick links</h3>
    <ul style="left:115px;top:44px"><li>About TAVO Sphere</li><li>Team</li><li>Supporters</li><li>Contributors</li></ul>
    <ul style="left:314px;top:44px"><li>Help</li><li>Contact us</li><li>For teachers</li><li>Volunteer</li></ul>
    <ul style="left:494px;top:44px"><li>Contributors</li><li>Jobs</li><li>Blog</li><li>User stories</li></ul>
    <h3 style="left:688px;top:18px">Folow us</h3>
    <ul class="social" style="left:686px;top:44px"><li><i></i>Friendspace</li><li><i></i>Chirper</li><li><i></i>Worknet</li><li><i></i>Searchly+</li></ul>
  </div>
  <div class="abs cta cta-donate"><i></i>Donate Now!</div>
  <div class="abs cta cta-volunteer"><i></i>Volunteer</div>
  <div class="abs bottom">© 2013 TAVO Sphere, All rights reserved</div>
</footer>

</body>
</html>
```